KRV Business Card

Looking for a business card for my restaurant group I own. Four different concepts:

Copperfield Alehouse
Bristow Alehouse
Tanager's Stone Hearth Kitchen
Pellston Patty Company

Card doesn't need to include all the logos.

```html
<!DOCTYPE html>
<html lang="en">
<head>
<meta charset="utf-8">
<title>KRV Business Card</title>
<link rel="stylesheet" href="https://fonts.googleapis.com/css2?family=Open+Sans:wght@400;600;700&display=swap">
<style>
  :root {
    --page-bg: #ebebeb;
    --card-bg: #1b1a1b;
    --gold: #c9af72;
    --slate: #77767b;
    --ink-light: #f2f2f2;
    --ghost: #242120;
  }
  * { margin: 0; padding: 0; box-sizing: border-box; }
  html, body {
    width: 1200px; height: 800px; overflow: hidden;
    background: var(--page-bg);
    font-family: "Open Sans", Arial, sans-serif;
  }
  .canvas { position: relative; width: 1200px; height: 800px; }
  .card {
    position: absolute; left: 316px; width: 570px; height: 330px;
    background: var(--card-bg); border-radius: 18px; overflow: hidden;
  }
  .card--front { top: 50px; }
  .card--back { top: 420px; }

  .ghost-initials {
    position: absolute; left: 28px; top: 38px;
    font-size: 96px; font-weight: 700; letter-spacing: 4px; line-height: 1;
    color: var(--ghost);
  }

  .brand-lockup {
    position: absolute; text-align: center; color: var(--gold); font-weight: 600;
  }
  .brand-lockup__initials { display: block; line-height: 1; letter-spacing: 3px; }
  .brand-lockup__name { display: block; text-transform: uppercase; line-height: 1.25; }

  .card--front .brand-lockup { right: 30px; top: 50px; width: 170px; }
  .card--front .brand-lockup__initials { font-size: 44px; }
  .card--front .brand-lockup__name { font-size: 15px; letter-spacing: 3px; margin-top: 10px; }

  .card--back .brand-lockup { left: 0; right: 0; top: 88px; }
  .card--back .brand-lockup__initials { font-size: 72px; letter-spacing: 6px; }
  .card--back .brand-lockup__name { font-size: 24px; letter-spacing: 5px; margin-top: 18px; }

  .holder {
    position: absolute; right: 25px; top: 186px; text-align: right;
  }
  .holder__name { color: var(--gold); font-size: 20px; font-weight: 700; line-height: 1.2; }
  .holder__company { color: var(--ink-light); font-size: 14px; margin-top: 6px; }
  .accent-tab {
    position: absolute; right: 0; top: 187px; width: 13px; height: 42px;
    background: var(--slate);
  }

  .contact-list { position: absolute; left: 30px; top: 232px; list-style: none; }
  .contact-list li {
    display: flex; align-items: center; height: 25px;
    color: var(--ink-light); font-size: 14.5px;
  }
  .contact-list svg { width: 16px; height: 16px; margin-right: 6px; flex: none; }
</style>
</head>
<body>
<main class="canvas">
  <section class="card card--front" aria-label="Card front">
    <div class="ghost-initials" aria-hidden="true">KRV</div>

    <div class="brand-lockup">
      <span class="brand-lockup__initials">KRV</span>
      <span class="brand-lockup__name">Kestrel Ridge Venues</span>
    </div>

    <div class="holder">
      <div class="holder__name">Dana Verhoef</div>
      <div class="holder__company">Kestrel Ridge Venues</div>
    </div>
    <div class="accent-tab"></div>

    <ul class="contact-list">
      <li>
        <svg viewBox="0 0 16 16" aria-hidden="true">
          <circle cx="8" cy="8" r="7.2" fill="none" stroke="var(--gold)" stroke-width="1"/>
          <path d="M5.3 4.6l1.3-.4.8 1.8-.8.6c.4.9 1 1.6 1.9 2l.6-.8 1.8.8-.4 1.3c-2.9.2-5.4-2.4-5.2-5.3z" fill="var(--gold)"/>
        </svg>555-014-2986
      </li>
      <li>
        <svg viewBox="0 0 16 16" aria-hidden="true">
          <circle cx="8" cy="8" r="7.2" fill="none" stroke="var(--gold)" stroke-width="1"/>
          <rect x="4.6" y="5.5" width="6.8" height="5" fill="var(--gold)"/>
          <path d="M4.6 5.5L8 8.3l3.4-2.8" fill="none" stroke="var(--card-bg)" stroke-width=".8"/>
        </svg>dana@krvrestaurants.com
      </li>
      <li>
        <svg viewBox="0 0 16 16" aria-hidden="true">
          <circle cx="8" cy="8" r="7.2" fill="none" stroke="var(--gold)" stroke-width="1"/>
          <circle cx="8" cy="8" r="3.6" fill="var(--gold)"/>
          <path d="M4.4 8h7.2M8 4.4c-1.5 2.2-1.5 5 0 7.2M8 4.4c1.5 2.2 1.5 5 0 7.2" fill="none" stroke="var(--card-bg)" stroke-width=".6"/>
        </svg>www.krvrestaurants.com
      </li>
    </ul>
  </section>

  <section class="card card--back" aria-label="Card back">
    <div class="brand-lockup">
      <span class="brand-lockup__initials">KRV</span>
      <span class="brand-lockup__name">Kestrel Ridge Venues</span>
    </div>
  </section>
</main>
</body>
</html>
```